Fence Contractor Website Design

We are working with Yard Shield. They are a local fencing and automatic gate installer and in need of a new website design.
Some sites to use for inspiration:
https://pelmorfence.example
https://tarvikfence.example
https://www.bristowdecksandfence.example
https://www.railquestinc.example
Thank you for taking the time to consider designing a website for us. We are web developers based in Stockton, CA, USA. Most of our projects go through the same process. Understanding this process may help you win a project with us. We custom-code all of our websites in-house. We don’t have any requirements as to what tools you use for your design, but we prefer Figma files. For any design that we label as four-stars, we send it to the client for review. The client picks the final design they want us to use. Once we complete this process, we will continue to show additional clients all the four-star sites and purchase them later. Your designs will have multiple chances to sell. For better chances of success, we ask that you follow these guidelines.
IMAGES:
If you use any images or icons in the design, we ask that you have a link to the asset so we can purchase the image/icon. Most of the designs we submit do not have the customer’s images on them unless they have some great images. Be creative; show us the feeling you are trying to portray with your image choices. Use any royalty-free site you choose. We subscribe to Veltrix and mainly use their images, but we can purchase images outside of Veltrix.
PLEASE NOTE: we will not submit designs to clients with watermarks on the images.
FONTS:
We ask that you identify the fonts used in the design. This can be done in a message if you want. We typically use Google Fonts and Veltrix Fonts.
CONTENT:
We're always open to different content and ideas. We often submit designs with stock images so the client can see our vision. We typically take pictures after the website launch to use their images with our vision. Lorem Ipsum is fine for paragraphs, but we ask that you write the headers in correct English. We want to be able to show the vision and identify the sections of the website.
INSPIRATION:
We typically add a couple of links in the brief of websites we like to help you get started in your design.
REVISIONS:
We do not often ask for revisions of the designs unless we see something in the design that may not appeal to the client. If there are slight changes that we want to make, we do that in the development process.
FEEDBACK:
We rarely give feedback on designs during the design process. We are working on many website projects and do not have the time to provide feedback. We usually respond if your request is well thought out and asks specific questions, but a note asking “feedback, please” usually goes unanswered.

```html
<!DOCTYPE html>
<html lang="en">
<head>
<meta charset="utf-8">
<title>Yard Shield – Fencing & Gates</title>
<link href="https://fonts.googleapis.com/css2?family=Oswald:wght@500;600;700&family=Montserrat:wght@400;500;600;700&display=swap" rel="stylesheet">
<style>
:root{
  --red:#e5111b;
  --red-dark:#a3060c;
  --ink:#1b1b1b;
  --text:#2c2c2c;
  --stone:#ececea;
  --stone-dark:#dcdcd8;
  --pink:#f2c8c8;
  --footer:#1a1a1a;
  --white:#fff;
}
*{box-sizing:border-box;margin:0;padding:0}
html,body{width:1200px;height:5213px;overflow:hidden}
body{position:relative;font-family:"Montserrat",sans-serif;color:var(--text);background:var(--stone)}
.abs{position:absolute}
.head{font-family:"Oswald",sans-serif;font-weight:600;text-transform:uppercase;color:var(--ink);letter-spacing:.2px}
.head em{font-style:normal;color:var(--red)}
.btn{position:absolute;background:var(--red);color:#fff;font-family:"Oswald",sans-serif;font-weight:600;text-transform:uppercase;font-size:14px;display:flex;align-items:center;justify-content:center;border-radius:3px}
.texture{background:radial-gradient(circle at 20% 30%,#f5f5f3 0,transparent 40%),radial-gradient(circle at 80% 70%,#e2e2df 0,transparent 45%),var(--stone)}

/* top bar */
.topbar{left:0;top:0;width:1200px;height:37px;background:#fff;font-size:11px;color:#333}
.topbar span{position:absolute;top:11px;display:flex;align-items:center;gap:8px}
.dot-ico{width:16px;height:16px;border-radius:50%;background:var(--red);display:inline-flex;align-items:center;justify-content:center}

/* nav */
.nav{left:0;top:37px;width:1200px;height:84px;background:#fff;border-top:1px solid #eee}
.brand{position:absolute;left:108px;top:22px;display:flex;align-items:center;gap:8px;font-family:"Oswald",sans-serif;font-weight:700;font-size:24px;color:var(--ink);text-transform:uppercase}
.brand i{width:22px;height:22px;background:var(--red);display:block}
.menu a{position:absolute;top:32px;font-family:"Oswald",sans-serif;font-weight:500;font-size:16px;color:var(--ink);text-decoration:none;text-transform:uppercase}
.menu a.active{color:var(--red)}
.agent{position:absolute;left:965px;top:0;width:235px;height:84px;background:var(--red);color:#fff;padding:20px 0 0 70px}
.agent small{display:block;font-size:10px;letter-spacing:2px;text-transform:uppercase}
.agent b{font-family:"Oswald",sans-serif;font-size:21px;font-weight:600}
.agent .ph{position:absolute;left:20px;top:22px;width:38px;height:38px;border-radius:50%;background:#fff;display:flex;align-items:center;justify-content:center}

/* hero */
.hero{left:0;top:121px;width:1200px;height:612px;background:linear-gradient(180deg,#3b2d2c 0,#6a4630 35%,#45301f 65%,#1e1a14 100%)}
.hero-title{position:absolute;left:107px;top:148px;font-size:46px;line-height:51px;color:#fff}
.hero .btn{left:107px;top:317px;width:181px;height:45px}
.dots{position:absolute;display:flex;gap:10px}
.dots i{width:13px;height:13px;border-radius:50%;border:1.5px solid #bbb;display:block}
.dots i.on{background:var(--red);border-color:var(--red)}

/* about */
.about{left:0;top:733px;width:1200px;height:558px}
.about .photo{position:absolute;left:0;top:0;width:610px;height:558px;background:linear-gradient(160deg,#8ca9c7 0,#b08040 45%,#c89658 70%,#4f8a35 100%);clip-path:polygon(0 0,100% 0,88% 100%,0 100%)}
.about h2{left:652px;top:118px;font-size:40px}
.about h3{left:652px;top:195px;font-size:19px;font-weight:500}
.about p{left:652px;top:243px;width:420px;font-size:13.5px;line-height:25px}
.about .btn{left:652px;top:415px;width:114px;height:46px}

/* services */
.services{left:0;top:1291px;width:1200px;height:1130px}
.sec-title{position:absolute;left:0;width:1200px;text-align:center;font-size:40px}
.svc{position:absolute;width:305px;height:378px}
.svc .img{width:305px;height:313px;border-radius:4px}
.svc h4{font-family:"Oswald",sans-serif;font-weight:600;font-size:25px;text-transform:uppercase;color:var(--ink);text-align:center;margin-top:20px}
.svc.active{background:var(--red);border-radius:4px}
.svc.active h4{color:#fff;margin-top:16px}

/* why */
.why{left:0;top:2421px;width:1200px;height:346px;background:linear-gradient(110deg,#c10912 0,#8d0309 40%,#e0131c 75%,#a2060c 100%)}
.why h2{position:absolute;left:0;top:110px;width:1200px;text-align:center;color:#fff;font-size:40px}
.why p{position:absolute;left:280px;top:170px;width:640px;text-align:center;color:#fff;font-size:14.5px;line-height:25px}

/* blogs */
.blogs{left:0;top:2767px;width:1200px;height:759px;background:var(--pink)}
.blog{position:absolute;top:192px;width:475px;height:393px;border-radius:6px;background:linear-gradient(140deg,#2a2521 0,#4a3a2c 50%,#1f1c19 100%);color:#fff;padding:78px 44px 0}
.blog h3{font-family:"Oswald",sans-serif;font-weight:600;font-size:34px;line-height:40px;text-transform:uppercase}
.blog p{font-size:13.5px;line-height:23px;margin-top:18px;width:385px}
.blog .btn{left:44px;top:277px;width:105px;height:44px;font-size:12px}
.blogs .all{left:547px;top:639px;width:106px;height:44px;font-size:12px}

/* instagram */
.insta{left:0;top:3526px;width:1200px;height:563px}
.ig{position:absolute;top:186px;height:257px}

/* contact */
.contact{left:0;top:4089px;width:1200px;height:671px}
.contact .rule{position:absolute;left:545px;top:124px;width:110px;height:2px;background:var(--red)}
.form-card{position:absolute;left:158px;top:165px;width:886px;height:393px;background:#fff;border-radius:0 0 60px 40px;box-shadow:0 10px 30px rgba(0,0,0,.12)}
.form-card h3{position:absolute;left:20px;top:18px;font-size:21px}
.field{position:absolute;width:220px;border-bottom:1px solid #c33;padding-bottom:6px}
.field label{display:block;font-size:10px;color:#555}
.field div{font-size:13px;color:#222;margin-top:4px}
.send{position:absolute;left:435px;top:280px;width:66px;height:66px;border-radius:50%;background:#1b1b1b;display:flex;align-items:center;justify-content:center}
.info{position:absolute;left:532px;top:-10px;width:354px;height:403px;background:var(--red);border-radius:0 0 0 50px;color:#fff}
.info h3{position:absolute;left:30px;top:32px;font-size:21px;color:#fff}
.info .row{position:absolute;left:30px;display:flex;align-items:center;gap:22px;font-size:13px;font-weight:600}
.soc{position:absolute;top:310px;width:26px;height:26px;border-radius:50%;background:#fff}

/* footer */
.footer{left:0;top:4760px;width:1200px;height:453px;background:var(--footer);color:#ddd}
.flogo{position:absolute;left:156px;top:170px;display:flex;align-items:center;gap:10px;font-family:"Oswald",sans-serif;font-weight:700;font-size:34px;color:#fff;text-transform:uppercase}
.flogo i{width:28px;height:28px;background:#fff;display:block}
.fcol{position:absolute;top:88px}
.fcol h5{font-size:18px;font-weight:700;color:#fff}
.fcol .u{width:40px;height:2px;background:var(--red);margin:8px 0 18px}
.fcol a{display:block;font-size:12px;color:#ddd;text-decoration:none;line-height:26px}
.fbottom{position:absolute;top:373px;font-size:11.5px;color:#ddd}
</style>
</head>
<body>

<div class="abs topbar">
  <span style="left:124px"><i class="dot-ico"><svg width="8" height="10" viewBox="0 0 8 10"><path d="M4 0a3.5 3.5 0 0 0-3.5 3.5C.5 6 4 10 4 10s3.5-4 3.5-6.5A3.5 3.5 0 0 0 4 0z" fill="#fff"/></svg></i>48 North Elm Street, Suite 4 Brookvale, WI 53999 USA</span>
  <span style="left:735px"><i class="dot-ico"><svg width="9" height="9" viewBox="0 0 10 10"><circle cx="5" cy="5" r="4" fill="none" stroke="#fff" stroke-width="1.4"/><path d="M5 2.5V5l2 1" stroke="#fff" stroke-width="1.2" fill="none"/></svg></i>Mon - Fri: 7:30 AM - 5:15 PM</span>
  <span style="left:958px"><i class="dot-ico"><svg width="9" height="7" viewBox="0 0 10 8"><rect x=".5" y=".5" width="9" height="7" fill="none" stroke="#fff"/><path d="M.5.5 5 4.5 9.5.5" stroke="#fff" fill="none"/></svg></i>info@yardshield.example</span>
</div>

<header class="abs nav">
  <div class="brand"><i></i>Yard Shield</div>
  <nav class="menu">
    <a class="active" style="left:403px">Home</a>
    <a style="left:475px">About</a>
    <a style="left:553px">Services</a>
    <a style="left:649px">Industries</a>
    <a style="left:760px">Careers</a>
    <a style="left:852px">Contact Us</a>
  </nav>
  <div class="agent">
    <div class="ph"><svg width="20" height="20" viewBox="0 0 24 24"><path d="M6.6 10.8a15 15 0 0 0 6.6 6.6l2.2-2.2a1 1 0 0 1 1-.25 11.4 11.4 0 0 0 3.6.6 1 1 0 0 1 1 1V20a1 1 0 0 1-1 1A17 17 0 0 1 3 4a1 1 0 0 1 1-1h3.5a1 1 0 0 1 1 1c0 1.25.2 2.45.6 3.6a1 1 0 0 1-.25 1z" fill="#e5111b"/></svg></div>
    <small>Talk to an agent</small>
    <b>888.888.8888</b>
  </div>
</header>

<section class="abs hero" role="img" aria-label="Modern home at sunset with a long horizontal wood slat fence and gate">
  <h1 class="head hero-title">Strong, Secure &amp; Stylish<br>Fencing Solutions<br>You Can Trust</h1>
  <a class="btn">Get a Free Quote</a>
  <div class="dots" style="left:107px;top:558px"><i></i><i></i><i class="on"></i></div>
</section>

<section class="abs about texture">
  <div class="photo" role="img" aria-label="Cedar privacy fence with lattice top in a suburban yard"></div>
  <h2 class="abs head">About <em>Us</em></h2>
  <h3 class="abs head">Over 20 Years of Fence Excellence</h3>
  <p class="abs">Gaerspiciatis unde omnis iste natus error sit voluptatem accusantium doloremque laudantium, totam rem aperiam, eaque ipsa quae ab illo inventore veritatis et quasi architecto beatae vitae dicta sunt explicabo. Nemo enim ipsam voluptatem quia voluptas sit aspernatur aut odit aut fugit, sed quia.</p>
  <a class="btn">Learn More</a>
</section>

<section class="abs services texture">
  <h2 class="head sec-title" style="top:90px">Our <em>Services</em></h2>
  <div class="svc" style="left:111px;top:201px"><div class="img" role="img" aria-label="White picket fences along a row of houses" style="background:linear-gradient(180deg,#5c8fd6,#e8eef4 60%,#b9c3cc)"></div><h4>Residential Fencing</h4></div>
  <div class="svc" style="left:447px;top:201px"><div class="img" role="img" aria-label="Steel barricade fencing outside a commercial building" style="background:linear-gradient(180deg,#4a4d50,#8a8c8e 55%,#6d6a66)"></div><h4>Commercial Fencing</h4></div>
  <div class="svc" style="left:783px;top:201px"><div class="img" role="img" aria-label="Dark slatted automatic sliding gate beside a stone wall" style="background:linear-gradient(180deg,#6d6b66,#2f3a3e 45%,#8c8a86)"></div><h4>Automatic Gates</h4></div>
  <div class="svc" style="left:111px;top:616px"><div class="img" role="img" aria-label="Custom wooden deck railing with balusters" style="background:linear-gradient(180deg,#4e7a3a,#b98447 45%,#d7a468)"></div><h4>Custom Fencing</h4></div>
  <div class="svc active" style="left:447px;top:616px"><div class="img" role="img" aria-label="Gloved hand repairing chain link fence" style="background:linear-gradient(140deg,#2c3f5c,#5a6270 50%,#c6602a)"></div><h4>Repairs &amp; Maintenance</h4></div>
  <div class="svc" style="left:783px;top:616px"><div class="img" role="img" aria-label="Two fence consultants talking outdoors" style="background:linear-gradient(160deg,#6d7e3e,#3d3528 50%,#8c7752)"></div><h4>Kosice Soeicnsle</h4></div>
</section>

<section class="abs why" role="img" aria-label="Red toned photo of a white picket fence casting shadows">
  <h2 class="head">Why Us?</h2>
  <p>Gaerspiciatis unde omnis iste natus error sit voluptatem accusantium doloremque laudantium, totam rem aperiam, eaque ipsa quae ab illo inventore veritatis et quasi architecto beatae vitae dicta sun.</p>
</section>

<section class="abs blogs">
  <h2 class="head sec-title" style="top:92px">Latest <em>Blogs</em></h2>
  <article class="blog" style="left:111px" role="img" aria-label="Worker installing a fence post at dusk">
    <h3>Perspiciatis unde omnis iste natus error sit</h3>
    <p>Gaerspiciatis unde omnis iste natus error sit voluptatem accusantium doloremque laudantium, totam rem aperiam, eaque ipsa quae ab illo inventore veritatis et quasi architecto beatae.</p>
    <a class="btn">Learn More</a>
  </article>
  <article class="blog" style="left:614px" role="img" aria-label="Worker measuring a fence line in a field">
    <h3>Perspiciatis unde omnis iste natus error sit</h3>
    <p>Gaerspiciatis unde omnis iste natus error sit voluptatem accusantium doloremque laudantium, totam rem aperiam, eaque ipsa quae ab illo inventore veritatis et quasi architecto beatae.</p>
    <a class="btn">Learn More</a>
  </article>
  <a class="btn all">View All Blogs</a>
</section>

<section class="abs insta texture">
  <h2 class="head sec-title" style="top:100px">Our <em>Instagram</em></h2>
  <div class="ig" role="img" aria-label="Faded wooden picket fence" style="left:0;width:222px;background:linear-gradient(90deg,#e9dccb,#cdb598);opacity:.6"></div>
  <div class="ig" role="img" aria-label="Hammer driving a nail into a fence board" style="left:246px;width:341px;background:linear-gradient(135deg,#7a5a2d,#c89248 50%,#3e4d2a);border:3px solid var(--red)"></div>
  <div class="ig" role="img" aria-label="White vinyl fence along a green lawn" style="left:613px;width:341px;background:linear-gradient(180deg,#7fa4d8,#e9eef1 45%,#5c8a3c)"></div>
  <div class="ig" role="img" aria-label="Worker building a rustic fence" style="left:979px;width:221px;background:linear-gradient(180deg,#c9c3b4,#9a8564);opacity:.6"></div>
  <div class="dots" style="left:565px;top:492px"><i></i><i class="on"></i><i></i><i></i></div>
</section>

<section class="abs contact texture">
  <h2 class="head sec-title" style="top:52px">Contact <em>Us</em></h2>
  <div class="rule"></div>
  <div class="form-card">
    <h3 class="head">Send Us a Message</h3>
    <svg class="abs" style="left:462px;top:20px" width="50" height="28" viewBox="0 0 50 28"><path d="M2 8h10M0 14h12M4 20h8" stroke="#222" stroke-width="2"/><rect x="16" y="3" width="32" height="22" fill="#f4c542" stroke="#222" stroke-width="2"/><path d="M16 3l16 12 16-12" fill="none" stroke="#222" stroke-width="2"/></svg>
    <div class="field" style="left:20px;top:68px;width:220px"><label>Your Name</label><div>Daniel Carter</div></div>
    <div class="field" style="left:270px;top:68px;width:220px"><label>Email Address</label><div>info.danielcarter.example</div></div>
    <div class="field" style="left:20px;top:145px;width:220px"><label>Phone</label><div>888 888 8888</div></div>
    <div class="field" style="left:270px;top:145px;width:220px"><label>Company</label><div>Marlow Oaks Company</div></div>
    <div class="field" style="left:20px;top:215px;width:400px;height:120px"><label>Enter Message</label><div>Hi, do you have a message to send?</div></div>
    <div class="send"><svg width="28" height="28" viewBox="0 0 24 24"><path d="M2 11 22 3l-6 18-4-7z" fill="#fff"/><path d="M12 14l10-11" stroke="#1b1b1b" stroke-width="1.5"/></svg></div>
    <div class="info">
      <h3 class="head">Contact Information</h3>
      <svg class="abs" style="left:292px;top:26px" width="34" height="32" viewBox="0 0 34 32"><path d="M17 2 2 15h4v15h22V15h4z" fill="#fff"/><circle cx="17" cy="19" r="5" fill="#e5111b"/></svg>
      <div class="row" style="top:92px"><svg width="26" height="26" viewBox="0 0 26 26"><rect x="3" y="5" width="20" height="18" fill="none" stroke="#fff" stroke-width="2"/><path d="M13 3a4 4 0 0 0-4 4c0 3 4 7 4 7s4-4 4-7a4 4 0 0 0-4-4z" fill="#fff"/></svg><span>2718 Willow Crest Lane, Ashford,<br>NY 10999, USA</span></div>
      <div class="row" style="top:168px;font-size:17px"><svg width="26" height="26" viewBox="0 0 26 26"><rect x="4" y="3" width="18" height="20" fill="none" stroke="#fff" stroke-width="2"/><path d="M8 8h10M8 13h10M8 18h6" stroke="#fff" stroke-width="2"/></svg><span>888.888.8888</span></div>
      <div class="row" style="top:232px;font-size:15px"><svg width="26" height="26" viewBox="0 0 26 26"><rect x="3" y="6" width="20" height="15" fill="none" stroke="#fff" stroke-width="2"/><path d="M3 6l10 8 10-8" fill="none" stroke="#fff" stroke-width="2"/></svg><span>info@yardshield.example</span></div>
      <i class="soc" style="left:30px"></i><i class="soc" style="left:72px"></i><i class="soc" style="left:114px"></i>
    </div>
  </div>
</section>

<footer class="abs footer">
  <div class="flogo"><i></i>Yard Shield</div>
  <div class="fcol" style="left:434px"><h5>Quick links</h5><div class="u"></div><a>Home</a><a>About</a><a>Services</a><a>Industries</a><a>Careers</a><a>Contact Us</a></div>
  <div class="fcol" style="left:645px"><h5>Links</h5><div class="u"></div><a>Copyright</a><a>Legal</a><a>Privacy</a><a>Accessibility</a><a>Sitemap</a></div>
  <div class="fcol" style="left:833px"><h5>Support</h5><div class="u"></div><a>FAQs</a><a>Privacy Policy</a><a>Terms of Service</a><a>Request a Quote</a><a>Client Login</a></div>
  <svg class="abs" style="left:1128px;top:300px" width="20" height="50" viewBox="0 0 20 50"><path d="M10 48V4M3 12l7-8 7 8" fill="none" stroke="#e5111b" stroke-width="2"/></svg>
  <div class="fbottom" style="left:111px">Copyright ©2025, All Rights Reserved</div>
  <div class="fbottom" style="left:861px">Terms of use</div>
  <div class="fbottom" style="left:971px">Privacy Policy</div>
</footer>

</body>
</html>
```